Business Card Design for Marketing Firm

Looking for business card design for higher end marketing firm. Clean but impressionable/trendy. We are a marketing firm that represents manufacturers in the foodservice equipment and supply industry. Our customers are end users such has hotels, restaurants, country clubs, convention centers and casinos as well as distributors of restaurants supplies and equipment, and manufacturers of foodservice equipment and supplies.
Target Market(s)
Hotels, Restaurants, Supply & Equipment Distributors, Foodservice Manufacturers
Industry/Entity Type
Foodservice/Hospitality
Contact Information for Business Card
Name, Title, Contact Number, Email, Website, Social Media, Address
Requirements
Must have
- Clean & Simple but Serious and Impressionable

```html
<!DOCTYPE html>
<html lang="en">
<head>
<meta charset="utf-8">
<title>Meridian Hospitality Reps – Business Card</title>
<link href="https://fonts.googleapis.com/css2?family=Open+Sans:wght@400;600;700&display=swap" rel="stylesheet">
<style>
  :root {
    --page-bg: #d9d1c6;
    --card-bg: #ece7e0;
    --card-edge: #f6f3ef;
    --ink: #24256b;
    --ink-soft: #2f2f3a;
  }
  html, body {
    margin: 0;
    padding: 0;
    width: 1200px;
    height: 1047px;
    overflow: hidden;
    background: var(--page-bg);
    font-family: "Open Sans", Arial, sans-serif;
  }
  .business-card {
    position: absolute;
    left: 100px;
    top: 250px;
    width: 1000px;
    height: 547px;
    border-radius: 26px;
    background: var(--card-bg);
    box-shadow: inset 0 0 0 2px var(--card-edge), 0 10px 30px rgba(60, 45, 30, 0.18);
    color: var(--ink);
  }
  .brand {
    position: absolute;
    left: 100px;
    top: 150px;
    width: 447px;
    text-align: center;
  }
  .brand-mark {
    display: block;
    margin: 0 auto 26px;
  }
  .brand-name {
    margin: 0;
    font-size: 33px;
    font-weight: 600;
    letter-spacing: 1px;
    line-height: 1.15;
    color: var(--ink);
  }
  .divider {
    position: absolute;
    left: 581px;
    top: 140px;
    width: 3px;
    height: 268px;
    background: var(--ink);
  }
  .contact-block {
    position: absolute;
    left: 612px;
    top: 136px;
  }
  .person-name {
    margin: 0;
    font-size: 34px;
    font-weight: 700;
    line-height: 1.1;
    color: var(--ink);
  }
  .person-title {
    margin: 4px 0 0;
    font-size: 23px;
    color: var(--ink-soft);
  }
  .contact-list {
    list-style: none;
    margin: 22px 0 0;
    padding: 0;
    font-size: 24px;
    color: var(--ink-soft);
  }
  .contact-list li {
    display: flex;
    align-items: center;
    height: 32px;
  }
  .contact-icon {
    width: 22px;
    height: 22px;
    margin-right: 8px;
    flex: none;
  }
  .address {
    margin: 22px 0 0;
    font-size: 24px;
    line-height: 32px;
    color: var(--ink-soft);
  }
  .social-row {
    position: absolute;
    left: 550px;
    top: 458px;
    display: flex;
    align-items: center;
  }
  .social-label {
    font-size: 34px;
    font-weight: 600;
    color: var(--ink);
    margin-right: 26px;
  }
  .social-dot {
    width: 27px;
    height: 27px;
    border-radius: 50%;
    background: var(--ink);
    margin-right: 8px;
  }
</style>
</head>
<body>
  <section class="business-card">
    <div class="brand">
      <svg class="brand-mark" width="64" height="64" viewBox="0 0 64 64" aria-hidden="true">
        <circle cx="32" cy="32" r="29" fill="none" stroke="var(--ink)" stroke-width="3"/>
      </svg>
      <p class="brand-name">MERIDIAN HOSPITALITY<br>REPS</p>
    </div>

    <div class="divider"></div>

    <div class="contact-block">
      <h1 class="person-name">DANIEL HART</h1>
      <p class="person-title">Managing Director</p>
      <ul class="contact-list">
        <li>
          <svg class="contact-icon" viewBox="0 0 24 24" aria-hidden="true">
            <path d="M6.6 10.8c1.4 2.8 3.8 5.1 6.6 6.6l2.2-2.2c.3-.3.7-.4 1-.2 1.1.4 2.3.6 3.6.6.6 0 1 .4 1 1V20c0 .6-.4 1-1 1C10.6 21 3 13.4 3 4c0-.6.4-1 1-1h3.5c.6 0 1 .4 1 1 0 1.3.2 2.5.6 3.6.1.3 0 .7-.2 1z" fill="var(--ink)"/>
          </svg>
          123 456 789
        </li>
        <li>
          <svg class="contact-icon" viewBox="0 0 24 24" aria-hidden="true">
            <rect x="3" y="6" width="18" height="13" rx="2" fill="none" stroke="var(--ink)" stroke-width="2"/>
            <path d="M3 7l9 6 9-6" fill="none" stroke="var(--ink)" stroke-width="2"/>
          </svg>
          info@yourmail.com
        </li>
        <li>
          <svg class="contact-icon" viewBox="0 0 24 24" aria-hidden="true">
            <circle cx="12" cy="12" r="9" fill="none" stroke="var(--ink)" stroke-width="2"/>
            <path d="M3 12h18M12 3c3 3 3 15 0 18M12 3c-3 3-3 15 0 18" fill="none" stroke="var(--ink)" stroke-width="1.6"/>
          </svg>
          www.yourwebsite.com
        </li>
      </ul>
      <p class="address">Your address, City<br>State, Zip 1234</p>
    </div>

    <div class="social-row">
      <span class="social-label">Follow Us</span>
      <span class="social-dot"></span>
      <span class="social-dot"></span>
      <span class="social-dot"></span>
      <span class="social-dot"></span>
      <span class="social-dot"></span>
      <span class="social-dot"></span>
    </div>
  </section>
</body>
</html>
```